Wordpress 6 pages GLAM design for hair salon

Hi guys.
I need a glam & easy to navigate web design for my (women only) new hair salon.
I have a logo. You can see in attached files.
I like 3d backgrounds.
My favourite colours choice: any variety of pink(hot & very soft), white, black, grey.
I would like to see website very feminine, glamorous & kind of old Hollywood and Dorinda Calloway inspired.
Of course it should have plug ins, like social media, map, security etc.
My website now: http://velmoracoiffure.example

Designs what I like:
http://torvinellastudio.example
http://pelurabeautyloft.example
http://www.quillfernvisualworks.example/boutique-graphic-web-folio.html
Updates

Target Market(s)

WOMEN

Industry/Entity Type

Boutique

Requirements
Should not have
• any cartoon or other characters!

```html
<!DOCTYPE html>
<html lang="en">
<head>
<meta charset="utf-8">
<title>Velmora Coiffure</title>
<link rel="stylesheet" href="https://fonts.googleapis.com/css2?family=Open+Sans:ital,wght@0,400;0,600;1,400&family=Pinyon+Script&display=swap">
<style>
:root{
  --pink:#d6387a;
  --hot:#c2185b;
  --soft:#f8dbe6;
  --soft-2:#f3c9d8;
  --paper:#f6f6f6;
  --ink:#222222;
  --text:#6b6b6b;
  --line:#dcdcdc;
  --white:#ffffff;
}
*{box-sizing:border-box;margin:0;padding:0}
html,body{width:1200px;height:1114px;overflow:hidden}
body{position:relative;font-family:"Open Sans",Arial,sans-serif;color:var(--text)}
.backdrop{position:absolute;inset:0;background:radial-gradient(circle at 50% 40%,var(--soft) 0%,var(--soft-2) 100%)}
.page-shape{position:absolute;left:0;top:0}
.brand{position:absolute;left:0;width:1200px;top:92px;text-align:center;font-weight:600;font-size:32px;line-height:38px;color:var(--pink);letter-spacing:1px}
.nav{position:absolute;left:149px;top:238px;width:906px;display:flex;justify-content:space-between;padding:0 20px 0 30px}
.nav a{font-size:21px;color:var(--ink);text-decoration:none;width:80px;text-align:center;white-space:nowrap}
.nav a::first-letter{color:var(--pink)}
.nav-rule{position:absolute;left:149px;top:304px;width:906px;height:4px;background:var(--ink)}
.nav-active{position:absolute;left:169px;top:304px;width:80px;height:4px;background:var(--pink)}
.hero{position:absolute;left:149px;top:315px;width:906px;height:238px;overflow:hidden;background:linear-gradient(100deg,#0c0a0a 0%,#3a1208 35%,#8a3418 55%,#2a1410 80%,#0e0b0b 100%)}
.hero-caption{position:absolute;left:0;top:143px;width:440px;height:56px;background:rgba(120,20,60,.65);color:#e9d3dc;font-size:17.5px;line-height:56px;padding-left:13px;white-space:nowrap;overflow:hidden}
.hero-dots{position:absolute;right:16px;bottom:13px;display:flex;gap:6px}
.hero-dots span{width:9px;height:9px;border-radius:50%;background:#ddd}
.hero-dots span.on{background:var(--pink);border:1px solid #fff}
.script{font-family:"Pinyon Script",cursive;color:var(--pink);font-weight:400;white-space:nowrap}
.welcome{position:absolute;left:150px;top:560px;font-size:31px}
.intro{position:absolute;left:150px;top:613px;width:450px;font-size:11.8px;line-height:19.7px}
.intro p+p{margin-top:19.7px}
.read-more{position:absolute;left:480px;top:742px;width:101px;text-align:right;font-size:12px;color:var(--pink)}
.compare{position:absolute;left:651px;top:568px;width:405px;height:189px;border:1px solid #cfcfcf;background:var(--white)}
.shot{position:absolute;top:5px;width:194px;height:177px;background:linear-gradient(160deg,#c9a07a 0%,#a77f5c 60%,#3b2a22 100%)}
.shot.before{left:6px}
.shot.after{left:207px}
.shot-label{position:absolute;right:0;bottom:0;background:var(--hot);color:#fff;font-size:12px;padding:2px 7px}
.posts-title{position:absolute;left:652px;top:795px;font-size:29px}
.post{position:absolute;left:651px;width:405px;height:87px;background:var(--white);border:1px solid #e6e6e6;padding:14px 16px;overflow:hidden}
.post time{display:block;font-style:italic;font-size:20px;color:#4a4a4a;white-space:nowrap}
.post a{display:block;margin-top:7px;font-size:11.8px;color:var(--ink);text-decoration:none;white-space:nowrap}
.post.one{top:840px}
.post.two{top:952px;padding-left:18px;padding-right:4px}
.more-post{position:absolute;left:950px;top:1048px;width:106px;text-align:right;font-size:12px;color:var(--pink)}
.book{position:absolute;left:152px;top:855px;width:420px;height:57px;background:var(--ink);color:#e8e8e8;font-size:20px;line-height:57px;text-align:center;white-space:nowrap;box-shadow:0 3px 4px rgba(0,0,0,.35);border-radius:2px}
.social{position:absolute;top:950px;width:56px;height:56px;border-radius:50%;background:radial-gradient(circle at 40% 35%,#f06bc0 0%,#c2148e 70%,#8e0f68 100%);border:3px solid #eee;box-shadow:0 3px 5px rgba(0,0,0,.25)}
.social.one{left:165px}
.social.two{left:513px}
.find-us{position:absolute;left:305px;top:962px;font-size:30px}
.footer{position:absolute;left:131px;top:1080px;width:941px;height:34px;background:var(--ink);color:#e0e0e0;font-size:10.5px;line-height:34px;text-align:center;font-family:Arial,sans-serif}
</style>
</head>
<body>
<div class="backdrop" role="img" aria-label="Soft pink scalloped pattern background with floral corner flourishes"></div>
<svg class="page-shape" width="1200" height="1114" viewBox="0 0 1200 1114" aria-hidden="true">
  <path d="M131,1114 V300 C131,210 240,190 295,125 C335,75 360,18 430,18 H770 C840,18 865,75 905,125 C960,190 1072,210 1072,300 V1114 Z" fill="#f6f6f6" stroke="#e8c6d3" stroke-width="2"/>
</svg>

<div class="brand">VELMORA<br>COIFFURE</div>

<nav class="nav">
  <a>Home</a><a>About</a><a>Services</a><a>Gallery</a><a>Blog</a><a>Contact</a>
</nav>
<div class="nav-rule"></div>
<div class="nav-active"></div>

<section class="hero" role="img" aria-label="Slideshow photo of a woman with windswept red hair on a black background">
  <div class="hero-caption">Our Team Is Committed to Meeting Those Needs</div>
  <div class="hero-dots"><span class="on"></span><span></span><span></span></div>
</section>

<h1 class="welcome script">Welcome To Velmora Coiffure</h1>
<div class="intro">
  <p>Our salon is based on the belief that our customers' needs are of the utmost importance. Our team is committed to meeting those needs. As a result, a high percentage of our business is from repeat customers and referrals.</p>
  <p>We would welcome the opportunity to earn your trust and deliver you the best service in the industry!</p>
</div>
<div class="read-more">Read More</div>

<div class="compare">
  <div class="shot before" role="img" aria-label="Before photo of a client with loose dark curls"><span class="shot-label">Before</span></div>
  <div class="shot after" role="img" aria-label="After photo of the client with a styled updo"><span class="shot-label">After</span></div>
</div>

<h2 class="posts-title script">Recent Posts</h2>
<article class="post one"><time>January 6, 2014</time><a>Permanent Link to How to Choose the Right Hair Spray</a></article>
<article class="post two"><time>December 14, 2013</time><a>Permanent Link to Shampoo: How Much Do You Really Need to Spend?</a></article>
<div class="more-post">More Post</div>

<div class="book">Book Your Appointment Online Now</div>
<div class="social one" aria-label="Social profile"></div>
<div class="find-us script">Find Us</div>
<div class="social two" aria-label="Social profile"></div>

<footer class="footer">Copyright of Velmora Coiffure all right reserved</footer>
</body>
</html>
```